Beauty Therapy Web Design

I need a web page design for a small beauty therapy clinic, the owner is currently the only beauty therapist working there.
We require the following pages:
Home
About
Treatments
Nails
Courses
Contact
I will attach the clinics business card, treatment menu and signage so that you get a feeling for the branding colours etc.
This is the first website for the beauty therapist, she would like to attract new clients and also tourists that come in on the cruise ships. The thing that sets her apart from other clinics is that she welcomes texting for appointments.
I have selected refundable because I have never done this before so I don't know what to expect, I have the full intention of going through with it as long as I get a good design.
Feel free to ask for further information
Reason: Project extended as I am away for work and am unable to meet with the owner.
Target Market(s)
Females 18 to 50
Industry/Entity Type
Business
Look and feel

```html
<!DOCTYPE html>
<html lang="en">
<head>
<meta charset="utf-8">
<title>Serenya Beauty Therapy</title>
<link rel="stylesheet" href="https://fonts.googleapis.com/css2?family=Open+Sans:wght@400;600&family=Comic+Neue:wght@700&family=Ubuntu:wght@500;700&family=Sorts+Mill+Goudy&family=Noto+Serif&family=Gentium+Book+Plus&display=swap">
<style>
:root{
  --bg:#eeebee;
  --bar:#000;
  --ink:#111;
  --grey-text:#8a8a8a;
  --rose:#d0235a;
  --magenta:#c43fd0;
  --crimson:#b32452;
  --panel-out:#b5acb7;
  --panel-in:#a89eab;
  --rule:#c9c4c9;
  --white:#fff;
}
*{margin:0;padding:0;box-sizing:border-box}
html,body{width:1200px;height:900px;overflow:hidden}
body{position:relative;background:linear-gradient(180deg,#f4f2f4 0%,var(--bg) 60%,#e9e6ea 100%);font-family:"Open Sans",sans-serif;color:var(--ink)}
.abs{position:absolute}
.top-bar{left:0;top:0;width:1200px;height:20px;background:var(--bar)}
.footer{left:0;top:833px;width:1200px;height:67px;background:var(--bar);color:var(--white);font-size:20px;display:flex;justify-content:space-between;align-items:center;padding:0 52px 0 53px}
.hero-photo{left:60px;top:20px;width:430px;height:230px;background:radial-gradient(ellipse at 45% 45%,#f0c9b7 0%,#e8bcaa 40%,#f4eef0 85%)}
.tagline-small{left:785px;top:28px;font-family:"Ubuntu",sans-serif;font-weight:700;font-size:22px}
.phone{left:1004px;top:26px;display:flex;align-items:center;gap:4px;font-size:17px;color:#555}
.welcome{left:529px;top:48px;font-size:38px;font-weight:400;letter-spacing:.3px}
.intro{left:533px;top:104px;width:600px;font-family:"Comic Neue",sans-serif;font-weight:700;font-size:13.6px;line-height:19.8px;color:var(--grey-text)}
.motto{left:532px;top:226px;font-family:"Comic Neue",sans-serif;font-weight:700;font-size:21px;color:var(--grey-text)}
.motto b{color:var(--magenta)}
.brand{left:62px;top:290px;display:flex;align-items:center;gap:10px;font-family:"Ubuntu",sans-serif;font-weight:700;font-size:40px;color:var(--magenta)}
.brand i{display:block;width:16px;height:16px;border-radius:50%;background:var(--magenta)}
.services-title{left:93px;top:390px;font-family:"Ubuntu",sans-serif;font-weight:500;font-size:25px;color:var(--rose)}
.services{left:71px;top:431px;width:196px;height:369px;border-radius:8px;background:var(--panel-out);box-shadow:1px 3px 4px rgba(0,0,0,.35);padding:9px}
.services ul{list-style:none;height:100%;border-radius:8px;background:var(--panel-in);box-shadow:inset 0 0 4px rgba(0,0,0,.35);padding:0 12px}
.services li{height:50px;display:flex;align-items:center;padding-left:0;border-bottom:1px solid #d8d2d9;font-family:"Sorts Mill Goudy",serif;font-size:23px;color:var(--white);text-shadow:1px 1px 2px #555}
.services li:last-child{border-bottom:none}
.nav{left:327px;top:291px;width:601px;height:66px;border-radius:8px;background:linear-gradient(180deg,#fdfdfd 0%,#ececec 55%,#cfcfcf 100%);box-shadow:1px 3px 4px rgba(0,0,0,.45);display:flex;align-items:center;padding-left:12px;font-family:"Ubuntu",sans-serif;font-weight:700;font-size:17.5px}
.nav a{color:var(--ink);text-decoration:none}
.nav a.current{color:var(--crimson);font-weight:500}
.nav .dot{width:9px;height:9px;border-radius:50%;background:var(--crimson);margin:0 9px 0 7px}
.about-copy{left:324px;top:381px;width:605px;font-family:"Comic Neue",sans-serif;font-weight:700;font-size:16px;line-height:19px;color:var(--grey-text)}
.about-copy p{margin-bottom:18px}
.divider{left:322px;top:570px;width:578px;height:1px;background:#b8b4b8}
.news-title{left:320px;top:576px;font-size:29px;color:var(--rose)}
.photo{border:0}
.news-photo-1{left:322px;top:616px;width:120px;height:146px;background:linear-gradient(90deg,#d9a88c 0%,#eac4ad 50%,#d7a184 100%)}
.news-photo-2{left:679px;top:618px;width:120px;height:144px;background:linear-gradient(160deg,#fff 0%,#f3ddd6 55%,#f2b8c6 100%)}
.offer-photo{left:937px;top:572px;width:213px;height:161px;background:linear-gradient(90deg,#6fb64c 0%,#e8c8a8 45%,#dfbd9c 70%,#8ec95b 100%)}
.btn{height:34px;border-radius:6px;background:linear-gradient(180deg,#5a5a5a 0%,#2a2a2a 50%,#111 100%);box-shadow:1px 2px 3px rgba(0,0,0,.4);color:var(--white);font-size:17px;display:flex;align-items:center;justify-content:center}
.btn-tans{left:448px;top:726px;width:115px}
.btn-facials{left:812px;top:726px;width:116px}
.btn-more{left:1035px;top:744px;width:115px}
.quote{left:325px;top:771px;width:615px;font-family:"Gentium Book Plus",serif;font-size:17px;line-height:30px;color:#666}
.side-head{font-family:"Noto Serif",serif;color:var(--rose);border-bottom:2px solid var(--rule)}
.hours-title{left:938px;top:360px;width:213px;font-size:23px;padding-bottom:2px}
.hours{left:946px;top:404px;font-family:"Comic Neue",sans-serif;font-weight:700;font-size:16px;color:var(--grey-text);border-collapse:collapse}
.hours td{height:22.5px;padding:0}
.hours td.day{width:90px;color:var(--rose);font-weight:400}
.offers-title{left:938px;top:513px;width:213px;font-size:29px;padding-bottom:2px}
</style>
</head>
<body>
<div class="abs top-bar"></div>

<div class="abs hero-photo photo" role="img" aria-label="Photo of manicured hands resting on pedicured feet with a white daisy"></div>

<div class="abs tagline-small">Beauty Therapy</div>
<div class="abs phone">
  <svg width="32" height="38" viewBox="0 0 32 38" aria-hidden="true">
    <g transform="rotate(-35 16 19)">
      <rect x="10" y="4" width="12" height="30" rx="3" fill="#cfd3d8" stroke="#777" stroke-width="1.2"/>
      <rect x="12" y="8" width="8" height="8" rx="1" fill="#8fa3b8"/>
      <rect x="12" y="19" width="8" height="11" rx="1" fill="#999"/>
    </g>
  </svg>
  <span>027-555-0142</span>
</div>
<h1 class="abs welcome">Welcome to Serenya</h1>
<p class="abs intro">Our Salon both belives and provides the Ultimate treatments in Skin Health and Beauty. Indulge and pamper yourself with our extensive range of facials, Body treatments, massage, and of course the all important nail cure, specilised Waxing and general Waxing and Eye Care. At Serenya We truely love and Passion for the beauty Industry and we Hope you try this at Serenya.</p>
<p class="abs motto">Be <b>adoerd</b>, Be <b>Pampered</b>, Be <b>Relaxed</b>, Be <b>Revived ...</b></p>

<div class="abs brand"><i></i>Serenya</div>

<h2 class="abs services-title">Our Services</h2>
<nav class="abs services" aria-label="Services">
  <ul>
    <li>~ Facial</li>
    <li>~ Waxing</li>
    <li>~ Gail Nails</li>
    <li>~ Manicures</li>
    <li>~ Eye Lash</li>
    <li>~ Eye Brow</li>
    <li>~ Spray Tants</li>
  </ul>
</nav>

<nav class="abs nav" aria-label="Main">
  <a class="current" href="#">HOME</a><span class="dot"></span>
  <a href="#">ABOUT</a><span class="dot" style="margin-left:13px;margin-right:17px"></span>
  <a href="#">NAILS</a><span class="dot" style="margin-left:7px;margin-right:5px"></span>
  <a href="#">TREATMENTS</a><span class="dot" style="margin-left:5px;margin-right:9px"></span>
  <a href="#">COURSES</a><span class="dot" style="margin-left:12px;margin-right:11px"></span>
  <a href="#">CONTACT US</a>
</nav>

<div class="abs about-copy">
  <p>At Serenya you will experience the Ultimate in all things beauty. Our Salon Invites you to Indulge and pamper yourself with our extensive rane of services including speciallized waxing. Skin rejunvenation, facials, nails and eye treatments.</p>
  <p>Our dedicated friendly therapist and technicians will ensure you experience the Ultimate in all thing beaut.</p>
  <p>So go on Treat yourself U deserved it...</p>
</div>
<div class="abs divider"></div>

<h2 class="abs news-title">Latest News</h2>
<div class="abs news-photo-1 photo" role="img" aria-label="Beauty portrait showing a spray tan result"></div>
<div class="abs btn btn-tans">Spray Tans</div>
<div class="abs news-photo-2 photo" role="img" aria-label="Beauty portrait with a pink lily for facials"></div>
<div class="abs btn btn-facials">Facials</div>
<p class="abs quote">“The thing that sets us apart from other clinics is that she welcomes texting for appointments.”</p>

<h2 class="abs side-head hours-title">Opening Timming</h2>
<table class="abs hours">
  <tr><td class="day">Tue</td><td>9am to 7pm</td></tr>
  <tr><td class="day">Wed-Fri</td><td>9:30am to 7pm</td></tr>
  <tr><td class="day">Stur</td><td>10am to 5:30pm</td></tr>
  <tr><td class="day">Sun</td><td>11am to 9pm</td></tr>
</table>

<h2 class="abs side-head offers-title">Special Offers</h2>
<div class="abs offer-photo photo" role="img" aria-label="Smiling woman holding frangipani flowers against a green garden background"></div>
<div class="abs btn btn-more">More &gt;&gt;&gt;</div>

<footer class="abs footer">
  <span>Address:&nbsp; C-7, Plot 215, Sunrise Gardens Lahore Pakistan.</span>
  <span>Copyright © Linewave Studio 2012</span>
</footer>
</body>
</html>
```